I need a SEO-friendly Wordpress website (making sure to style H1, H2, H3, etc correctly) for a Hawaii-based law firm called Meridian Crest Legal Group. Comparable websites include https://brvlaw.example/ and https://www.lomrit.example/ for design reference. The current copy on the TarnAdvocate.example website can be used.

```html
<!DOCTYPE html>
<html lang="en">
<head>
<meta charset="utf-8">
<title>Meridian Crest Legal Group — Kona Divorce and Personal Injury Lawyers</title>
<link href="https://fonts.googleapis.com/css2?family=Montserrat:wght@800&family=Mulish:wght@300;400;600;700&display=swap" rel="stylesheet">
<style>
:root{
  --brand:#a64a12;
  --brand-dark:#7d2c08;
  --ink:#222;
  --muted:#555;
  --grey:#e4e4e4;
  --white:#fff;
  --sea:#1f5a82;
  --land:#4d6b3a;
}
*{margin:0;padding:0;box-sizing:border-box}
html,body{width:1200px;height:2991px;overflow:hidden;background:var(--white)}
body{font-family:'Mulish',sans-serif;color:var(--ink)}
.page{position:relative;width:1200px;height:2991px;overflow:hidden}
.abs{position:absolute}
.btn{position:absolute;display:flex;align-items:center;justify-content:center;background:var(--brand);color:var(--white);font-weight:600;font-size:18px;text-decoration:none;letter-spacing:.2px}
.btn-outline{background:transparent;border:1.5px solid var(--white);font-size:14px;font-weight:700}

/* header */
.site-header{position:absolute;top:0;left:0;width:1200px;height:100px;background:var(--white)}
.brand-name{position:absolute;left:136px;top:14px;font-size:22px;font-weight:600;line-height:25px;text-transform:uppercase;color:var(--ink)}
.brand-tag{position:absolute;left:135px;top:67px;font-size:15.5px;color:var(--ink)}
.main-nav a{position:absolute;top:40px;font-size:16px;font-weight:700;color:var(--ink);text-decoration:none;text-transform:uppercase}
.main-nav a.active{color:var(--brand);padding-bottom:14px;border-bottom:2px solid var(--brand)}
.header-phone{position:absolute;left:946px;top:35px;font-size:20px;font-weight:700;color:var(--ink);display:flex;align-items:center;gap:4px}

/* hero */
.hero{position:absolute;top:100px;left:0;width:1200px;height:660px;background:linear-gradient(110deg,#3f5a34 0%,#55713f 35%,#3d6a70 55%,#1e5a86 75%,#173f6a 100%)}
.hero h1{position:absolute;top:166px;left:0;width:1212px;text-align:center;font-family:'Montserrat',sans-serif;font-weight:800;font-size:42px;line-height:43px;color:var(--white);text-transform:uppercase;text-shadow:0 2px 6px rgba(0,0,0,.35)}
.slider-dots span{position:absolute;left:1051px;width:14px;height:14px;border-radius:50%;background:var(--white)}
.slider-dots span.ring{background:transparent;border:2px solid var(--white)}

/* practice areas */
.practice-area{position:absolute;width:270px;height:270px;border-radius:50%;background:var(--white);box-shadow:0 6px 14px rgba(0,0,0,.2);text-align:center}
.practice-area h3{position:absolute;left:0;width:100%;font-size:18px;font-weight:600;line-height:24px;text-transform:uppercase;color:var(--ink)}
.practice-area svg.icon{position:absolute;left:50%;margin-left:-38px;top:48px}
.practice-area .chev{position:absolute;left:50%;margin-left:-19px;top:200px}
.practice-area.featured{background:radial-gradient(circle at 50% 40%,#a24a14,#7a2a08);width:274px;height:274px}
.practice-area.featured h3{color:var(--white);font-size:18px;line-height:21px}

/* about */
.about h2{position:absolute;top:900px;left:0;width:1200px;text-align:center;font-size:33px;font-weight:400;color:var(--ink)}
.about p{position:absolute;left:220px;width:760px;text-align:center;font-size:17px;line-height:22px;color:#333}

/* attorneys */
.attorneys h2{position:absolute;top:1318px;left:0;width:1224px;text-align:center;color:var(--white);font-size:33px;font-weight:400}
.attorney-photo{position:absolute;width:172px;height:172px;border-radius:50%;background:linear-gradient(160deg,#9a8a80,#5a4a44)}
.attorney h3{position:absolute;top:1399px;color:var(--white);font-size:20px;font-weight:700;text-transform:uppercase}
.attorney p{position:absolute;top:1431px;width:295px;color:var(--white);font-size:14px;line-height:23px;font-weight:400}

/* blogs */
.blogs h2{position:absolute;top:1752px;left:0;width:1196px;text-align:center;font-size:33px;font-weight:400}
.blog-image{position:absolute;top:1828px;width:421px;height:270px}
.blog-card h3{position:absolute;top:2113px;width:410px;font-size:22px;font-weight:400;line-height:29px;color:var(--ink)}
.blog-card p{position:absolute;top:2184px;width:420px;font-size:16px;line-height:25px;color:var(--muted)}
.blog-card .btn{font-size:15px;width:153px;height:41px;top:2272px}

/* contact */
.contact-map{position:absolute;top:2399px;left:0;width:1200px;height:439px;background:linear-gradient(100deg,#b7d3ea 0%,#d9e4d8 20%,#ececec 40%,#ececec 70%,#e3ecdf 100%)}
.contact-card{position:absolute;top:2487px;left:389px;width:418px;height:258px;background:var(--white);text-align:center}
.contact-card h2{font-size:32px;font-weight:400;margin-top:32px;margin-bottom:10px}
.contact-card address{font-style:normal;font-size:17px;line-height:32px;color:var(--ink)}

/* footer */
.site-footer nav a{position:absolute;top:2891px;font-size:17px;font-weight:700;color:var(--ink);text-decoration:none;text-transform:uppercase}
.copyright{position:absolute;left:142px;top:2927px;font-size:12px;color:var(--ink)}
.social span{position:absolute;top:2893px;width:18px;height:18px;border-radius:50%;background:var(--brand)}
</style>
</head>
<body>
<div class="page">

  <header class="site-header">
    <div class="brand-name">Meridian Crest<br>Legal Group</div>
    <div class="brand-tag">Divorce and Personal Injury Lawyer</div>
    <nav class="main-nav">
      <a class="active" href="#" style="left:429px">Practice Areas</a>
      <a href="#" style="left:602px">Attorneys</a>
      <a href="#" style="left:739px">Blog</a>
      <a href="#" style="left:823px">Contact Us</a>
    </nav>
    <div class="header-phone">
      <svg width="20" height="20" viewBox="0 0 24 24"><path fill="#a64a12" d="M6.6 10.8a15 15 0 0 0 6.6 6.6l2.2-2.2c.3-.3.7-.4 1-.2 1.1.4 2.3.6 3.6.6.6 0 1 .4 1 1V20c0 .6-.4 1-1 1A17 17 0 0 1 3 4c0-.6.4-1 1-1h3.5c.6 0 1 .4 1 1 0 1.3.2 2.5.6 3.6.1.3 0 .7-.2 1z"/></svg>
      1.808.555.0142
    </div>
  </header>

  <section class="hero">
    <div class="abs" role="img" aria-label="Aerial photograph of the Kona coastline with resort grounds and ocean" style="inset:0"></div>
    <h1>Dedicated to making sure<br>you receive the care and<br>attention you need</h1>
    <a class="btn" href="#" style="left:516px;top:308px;width:177px;height:49px">READ MORE</a>
    <div class="slider-dots">
      <span class="ring" style="top:233px"></span>
      <span style="top:255px"></span>
      <span style="top:277px"></span>
      <span style="top:299px"></span>
    </div>
  </section>

  <svg class="abs" style="left:0;top:620px" width="1200" height="600" viewBox="0 0 1200 600" aria-hidden="true">
    <defs><linearGradient id="greyFade" x1="0" y1="0" x2="0" y2="1"><stop offset="0" stop-color="#dcdcdc"/><stop offset=".45" stop-color="#f4f4f4"/><stop offset="1" stop-color="#fff"/></linearGradient></defs>
    <path d="M0 105 Q600 -10 1200 105 L1200 600 L0 600Z" fill="url(#greyFade)"/>
  </svg>

  <section class="practice-areas">
    <div class="practice-area" style="left:121px;top:560px">
      <svg class="icon" width="76" height="70" viewBox="0 0 76 70" fill="none" stroke="#a64a12" stroke-width="2.5"><circle cx="22" cy="14" r="9"/><circle cx="52" cy="14" r="9"/><circle cx="38" cy="42" r="7"/><path d="M6 68V40c0-8 6-12 16-12s14 4 14 8M70 68V40c0-8-6-12-18-12"/><path d="M28 68V58c0-4 4-6 10-6s10 2 10 6v10"/></svg>
      <h3 style="top:132px">Family &amp;<br>Divorce</h3>
      <svg class="chev" width="38" height="38" viewBox="0 0 38 38" fill="none" stroke="#555" stroke-width="1.5"><circle cx="19" cy="19" r="17"/><path d="M12 16l7 7 7-7"/></svg>
    </div>
    <div class="practice-area" style="left:342px;top:560px">
      <svg class="icon" width="76" height="70" viewBox="0 0 76 70" fill="none" stroke="#a64a12" stroke-width="2.5"><circle cx="16" cy="10" r="7"/><path d="M8 26l14 6 10 16-8 18M22 32l18-4M46 6h20v16c0 8-10 12-10 12s-10-4-10-12z"/><path d="M10 58l3 5 5-1-3 5"/></svg>
      <h3 style="top:132px">Personal<br>Injury</h3>
      <svg class="chev" width="38" height="38" viewBox="0 0 38 38" fill="none" stroke="#555" stroke-width="1.5"><circle cx="19" cy="19" r="17"/><path d="M12 16l7 7 7-7"/></svg>
    </div>
    <div class="practice-area featured" style="left:585px;top:558px">
      <svg class="icon" width="76" height="70" viewBox="0 0 76 70" fill="none" stroke="#fff" stroke-width="2.5"><rect x="18" y="6" width="40" height="60"/><path d="M26 16h4M34 16h4M42 16h4M50 16h0M26 26h4M34 26h4M42 26h4M26 36h4M34 36h4M42 36h4M26 46h4M34 46h4M42 46h4M34 66V56h8v10M2 66h72M8 66V48M68 66V48"/></svg>
      <h3 style="top:134px">Corporate &amp;<br>Intellectual<br>Property</h3>
      <svg class="chev" width="38" height="38" viewBox="0 0 38 38" fill="none" stroke="#fff" stroke-width="1.8" style="top:196px"><circle cx="19" cy="19" r="17"/><path d="M12 16l7 7 7-7"/></svg>
    </div>
    <div class="practice-area" style="left:810px;top:560px">
      <svg class="icon" width="76" height="70" viewBox="0 0 76 70" fill="none" stroke="#a64a12" stroke-width="2.5"><path d="M16 34L40 12l24 22M22 30v22h36V30M34 52V40h12v12M4 60h30l14-8 16-2"/></svg>
      <h3 style="top:132px">Real Estate</h3>
      <svg class="chev" width="38" height="38" viewBox="0 0 38 38" fill="none" stroke="#555" stroke-width="1.5"><circle cx="19" cy="19" r="17"/><path d="M12 16l7 7 7-7"/></svg>
    </div>
  </section>

  <section class="about">
    <h2>ABOUT THE KONA LAWYERS OF MCLG</h2>
    <p style="top:960px">The experienced attorneys in the Meridian Crest Legal Group's Kailua Kona, Hawaii office provide clients with a wide range of litigation expertise, including legal claims involving divorce &amp; family, personal injury, toxic exposures, intellectual property, and real estate.</p>
    <p style="top:1047px">Our Kona office also offers commercial and hospitality litigation expertise on behalf of a wide variety of clients, including restaurants, hotels, property owners, and many others.</p>
    <a class="btn" href="#" style="left:511px;top:1127px;width:177px;height:49px">READ MORE</a>
  </section>

  <section class="attorneys">
    <div class="abs" role="img" aria-label="Warm sunset sky over the ocean" style="left:0;top:1170px;width:1200px;height:522px;background:linear-gradient(180deg,#8a2f08 0%,#a2420f 45%,#b14f14 75%,#9a3d0c 100%)"></div>
    <svg class="abs" style="left:0;top:1168px" width="1200" height="100" viewBox="0 0 1200 100" aria-hidden="true"><path d="M0 0H1200V20Q600 150 0 10Z" fill="#fff"/></svg>
    <h2>OUR ATTORNEYS</h2>
    <article class="attorney">
      <div class="attorney-photo" role="img" aria-label="Portrait of attorney Daniel Ruvalo" style="left:119px;top:1387px"></div>
      <h3 style="left:309px">Daniel Ruvalo, Esq</h3>
      <p style="left:308px">Daniel Ruvalo graduated from the Harborview College of Law, in 1972.&nbsp; He graduated magna cum laude from Westmere University College of Law</p>
      <a class="btn btn-outline" href="#" style="left:309px;top:1540px;width:127px;height:36px">READ MORE</a>
    </article>
    <article class="attorney">
      <div class="attorney-photo" role="img" aria-label="Portrait of attorney Martin Keahi" style="left:622px;top:1387px;background:linear-gradient(160deg,#cfcfcf,#8f8f8f)"></div>
      <h3 style="left:812px">Martin Keahi, Esq.</h3>
      <p style="left:812px">Martin Keahi graduated from the Harborview College of Law, in 1971.&nbsp; He has over 35 years of experience as a litigator in both State</p>
      <a class="btn btn-outline" href="#" style="left:812px;top:1542px;width:128px;height:36px">READ MORE</a>
    </article>
  </section>

  <section class="blogs">
    <h2>OUR BLOGS</h2>
    <svg class="abs" style="left:82px;top:1932px" width="30" height="52" viewBox="0 0 30 52" fill="none" stroke="#444" stroke-width="2"><path d="M26 2L4 26l22 24"/></svg>
    <svg class="abs" style="left:1072px;top:1932px" width="30" height="52" viewBox="0 0 30 52" fill="none" stroke="#444" stroke-width="2"><path d="M4 2l22 24L4 50"/></svg>
    <article class="blog-card">
      <div class="blog-image" role="img" aria-label="Lawyer meeting an injured client wearing a neck brace" style="left:154px;background:linear-gradient(120deg,#c9d5e2,#e8e8e8 60%,#d8cbb8)"></div>
      <h3 style="left:161px">Auscipit leo massa sodales velit et scelerisqmi tortor at ipsum Proin</h3>
      <p style="left:159px">suscipit leo massa sodales velit et scelerisque mi tortor at ipsum Proin orci odio commodo ac gravida non tristique vel tellus Pellentesque nibh libero</p>
      <a class="btn" href="#" style="left:160px">READ MORE</a>
    </article>
    <article class="blog-card">
      <div class="blog-image" role="img" aria-label="Person wrapping a bandage around an injured arm" style="left:615px;background:linear-gradient(120deg,#4f6e3c,#7a9a58 45%,#2f5fa8 75%,#d9d9d6)"></div>
      <h3 style="left:622px">Auscipit leo massa sodales velit et scelerisqmi tortor at ipsum Proin</h3>
      <p style="left:620px">suscipit leo massa sodales velit et scelerisque mi tortor at ipsum Proin orci odio commodo ac gravida non tristique vel tellus Pellentesque nibh libero</p>
      <a class="btn" href="#" style="left:620px">READ MORE</a>
    </article>
  </section>

  <section class="contact">
    <div class="contact-map" role="img" aria-label="Street map of Kailua Kona showing the office location"></div>
    <div class="contact-card">
      <h2>CONTACT US</h2>
      <address>75-4120 Palani Court, Suite 210<br>Kailua Kona, Hawaii 96740.<br>+1.808.555.0142<br>clients@tarnadvocate.example</address>
    </div>
  </section>

  <footer class="site-footer">
    <nav>
      <a href="#" style="left:142px">Home</a>
      <a href="#" style="left:235px">Practice Areas</a>
      <a href="#" style="left:412px">Attorneys</a>
      <a href="#" style="left:552px">Blog</a>
      <a href="#" style="left:638px">Contact Us</a>
    </nav>
    <div class="copyright">© 2019 Company Name&nbsp; All right reserved</div>
    <div class="social">
      <span style="left:926px" aria-label="Social profile"></span>
      <span style="left:986px" aria-label="Social profile"></span>
      <span style="left:1044px" aria-label="Social profile"></span>
    </div>
  </footer>

</div>
</body>
</html>
```